July 2022 Industrial Manufacturer Product Expo Mexico City

We manufacture large screws and fastners for large Mining equipment, Trains, large ships, airplanes, wind turbines, and so on. We also do custom work base on the customer needs. No matter the size we can make it.
We have a Expo coming up with companies all over the world. We have to stand out we are a family own business so our customer service will be above and beyond anyone can provide. We do not have a sales force to push our products and services we provide one on one service.
Plus@!! I'm looking for anything that you designers can come up with if it was your company to put on a business card, plus i want to do a 1 or 2 sided pamphlet, and then a website. We make Speciality Bolts for large mining equipment these bolts can be 3 to 4 foot long!!! Plus fasteners, Nuts, washers, any, size, strengths, special materials, we offer more of a ono on one customer service, We are a small company, family own, but can fulfill any type of orders. We can also provide special time lines for emergency orders. "We keep the machines running we here at KRV don't believe in down time" We want to hear any slogan based on our company to stand out.
Thanks i really appreciate all your work and options that we have to pick on. Plus just a thought we could possibly want to entertain a experience Marketing internet help maybe a employment possibility. Thanks

I need 2 cards one in Spanish and English Like the steel back ground maybe send me in some bright red and blue writing Same with the Black cards Please remove the word Military The logo KRV maybe integrate a picture of a Bolt 🔩 Thank you

Still looking for I need 2 cards one in Spanish and English Like the steel back ground maybe send me in some bright red and blue writing Same with the Black cards try bright writing Please remove the word Military The logo KRV maybe integrate a picture of a Bolt 🔩 Plus will need the company to make a brochure and website next Thank you

Target Market(s)

Large Mining, Ship, Train, Green Energy, VELM, and Government equipment. Throughout the World

Industry/Entity Type

We can Custom Manufacture any type of Fastners for Mining equipment, Trains, Ships, Green energy, Governments, or military projects. wind turbines,

Contact Information for Business Card

I attached the name and contact info that's on a card, plus the Company Logo. Would like industrial looking background with Bright Colors that will stand out!! If we can insert somewhere maybe on back that we "Custom Manufacture Any Size or Quantity Fastners for Large Mining Equipment, Trains, Ships, Green Energy Equipment or Government Projects

Font styles to use
Other font styles liked:
• You Pick, has to be bold, colorful standout, Professional looking Beable to read it.

Colors

Designer to choose colors to be used in the design.

Requirements
Must have
• Need in Spanish and English TO STANDOUT FROM THE REST OF THE EXPO!! See Business card details, Rounded corners
Nice to have
• Can i see some of the darker cards with Bright Red and Blue letters I like to see the different type of card material, heavy thickness, plastic, transparent, Metal types, Bright Colors, I saw like Raised letters like on the logo.

```html
<!DOCTYPE html>
<html lang="es">
<head>
<meta charset="utf-8">
<title>KRV – Tarjetas de presentación</title>
<link rel="stylesheet" href="https://fonts.googleapis.com/css2?family=Source+Sans+3:wght@400;600;700&display=swap">
<style>
  :root {
    --backdrop: #1b1b1b;
    --kraft-light: #dcb78b;
    --kraft-mid: #bf8f5e;
    --kraft-dark: #94653a;
    --ink: #111111;
    --rule: #6e5237;
    --paper: #ffffff;
    --brand-blue: #0a5fae;
    --tagline-red: #cc1122;
  }
  * { margin: 0; padding: 0; box-sizing: border-box; }
  html, body {
    width: 1093px; height: 1200px; overflow: hidden;
    background: var(--backdrop);
    font-family: "Source Sans 3", "Myriad Pro", Arial, sans-serif;
  }
  .canvas { position: relative; width: 1093px; height: 1200px; }
  .card {
    position: absolute; left: 264px; width: 580px; height: 357px;
    text-align: center;
  }
  .card--front {
    top: 226px;
    background: linear-gradient(135deg, var(--kraft-light) 0%, var(--kraft-mid) 55%, var(--kraft-dark) 100%);
    color: var(--ink);
  }
  .card--back {
    top: 620px;
    background: var(--paper);
  }
  .brand {
    position: absolute; left: 0; right: 0;
    font-weight: 700; font-size: 96px; line-height: 1; letter-spacing: 14px;
  }
  .card--front .brand { top: 62px; color: var(--ink); }
  .card--back .brand { top: 68px; color: var(--brand-blue); }
  .holder {
    position: absolute; top: 186px; left: 0; right: 0;
    font-weight: 600; font-size: 21px;
  }
  .rule {
    position: absolute; left: 253px; width: 74px; height: 1px;
    background: var(--rule);
  }
  .rule--upper { top: 223px; }
  .rule--lower { top: 284px; }
  .quote-note {
    position: absolute; top: 230px; left: 0; right: 0;
    font-size: 16px; line-height: 22px;
  }
  .phones {
    position: absolute; top: 294px; left: 0; right: 0;
    font-size: 16px; display: flex; justify-content: center; align-items: center; gap: 4px;
  }
  .phones svg { width: 15px; height: 15px; }
  .phones .gap { margin-right: 2px; }
  .tagline {
    position: absolute; top: 228px; left: 0; right: 0;
    color: var(--tagline-red); font-size: 18.5px; line-height: 23.5px;
  }
</style>
</head>
<body>
<main class="canvas">
  <section class="card card--front">
    <div class="brand">KRV</div>
    <p class="holder">Lic. Mariela Ortiz Cano</p>
    <div class="rule rule--upper"></div>
    <p class="quote-note">Cotizaciones en<br>krvpernos.ventas@mail.com</p>
    <div class="rule rule--lower"></div>
    <p class="phones">
      <svg viewBox="0 0 24 24" aria-hidden="true"><path fill="#111" d="M6.6 10.8a15 15 0 0 0 6.6 6.6l2.2-2.2a1 1 0 0 1 1-.25 11.4 11.4 0 0 0 3.6.57 1 1 0 0 1 1 1V20a1 1 0 0 1-1 1A17 17 0 0 1 3 4a1 1 0 0 1 1-1h3.5a1 1 0 0 1 1 1c0 1.25.2 2.45.57 3.6a1 1 0 0 1-.25 1z"/></svg>
      <span class="gap">5550148822</span>
      <svg viewBox="0 0 24 24" aria-hidden="true"><rect x="6" y="2" width="12" height="20" rx="2" fill="none" stroke="#111" stroke-width="2.4"/><rect x="10" y="17" width="4" height="2" fill="#111"/></svg>
      <span>5550193377</span>
    </p>
  </section>

  <section class="card card--back">
    <div class="brand">KRV</div>
    <p class="tagline">Custom Manufacture Any Size or<br>Quantity Fastners for Large&nbsp; Mining<br>Equipment Trains, Ships, Green Energy<br>Equipment or Government Projects</p>
  </section>
</main>
</body>
</html>
```